Music Studio and Store Business Card and Logo Design

We need a business card and logo design for an existing Music Studio (Piano and Voice) which will soon expand to offer retail sheet music for all instruments including voice. The expanding store will not sell or lease instruments. We are a well known Fine Arts Studio for instruction to children, college students, and adults with 42 enrolled students and a wait list. We want something with simple elegance, but not archaic. Even a sleek modern look is okay. We do not want something childish or too fun looking because we do serve ages 5 - 62. We would also like the logo workable/transferable to signage for our new location opening in March. We like classic burgundy, black, deep blues, but are open to other suggestions. We included our studio brochure so you can get to know us a little better and some images we thought were interesting with the use of clef signs for the & and using note heads for the bottom or top of the letter "H"

Target Market(s)

All ages

Industry/Entity Type

Business

Contact Information for Business Card

H&H Music StudioPlattsburgh, NYWanda J. Haby and Oren M. Castaldi, Owners

Requirements
Must have
• Phone Number: (555) 817-4062
• Website: www.rbtonalartsroom.example
Nice to have
• Email: lorna@rbtonalartsroom.example
Should not have
• Any instruments on the card other than piano. Instrument pix is not a necessity.

```html
<!DOCTYPE html>
<html lang="en">
<head>
<meta charset="utf-8">
<title>R&amp;B Music Studio – Business Card</title>
<link rel="stylesheet" href="https://fonts.googleapis.com/css2?family=Didact+Gothic&family=Source+Sans+3:wght@400;700&display=swap">
<style>
  :root {
    --backdrop-top: #2b2b2b;
    --backdrop-bottom: #000000;
    --card-front: #f3f3f3;
    --card-back: #ffffff;
    --ink: #111111;
    --ink-soft: #222222;
    --emboss: #ececec;
  }
  * { margin: 0; padding: 0; box-sizing: border-box; }
  html, body {
    width: 1200px;
    height: 900px;
    overflow: hidden;
  }
  body {
    background: linear-gradient(to bottom, var(--backdrop-top), var(--backdrop-bottom));
    position: relative;
    color: var(--ink);
  }
  .card {
    position: absolute;
    top: 184px;
    height: 490px;
    border-radius: 12px;
    overflow: hidden;
  }
  .card--front {
    left: 299px;
    width: 301px;
    background: var(--card-front);
  }
  .card--back {
    left: 645px;
    width: 304px;
    background: var(--card-back);
  }
  .brand-mark,
  .brand-tagline,
  .brand-watermark {
    position: absolute;
    left: 0;
    right: 0;
    text-align: center;
    white-space: nowrap;
    font-family: "Didact Gothic", "Century Gothic", sans-serif;
    font-weight: 400;
    line-height: 1;
  }
  .card--front .brand-mark {
    top: 66px;
    font-size: 58px;
    color: var(--ink);
  }
  .card--front .brand-tagline {
    top: 156px;
    font-size: 34px;
    color: var(--ink);
  }
  .card--back .brand-watermark {
    top: 130px;
    font-size: 130px;
    color: var(--emboss);
  }
  .card--back .brand-tagline {
    top: 414px;
    font-size: 38px;
    color: var(--ink);
  }
  .contact,
  .owners,
  .location {
    position: absolute;
    left: 0;
    right: 0;
    text-align: center;
    font-family: "Source Sans 3", "Myriad Pro", sans-serif;
    color: var(--ink-soft);
  }
  .contact {
    top: 232px;
    font-size: 13px;
    line-height: 19px;
  }
  .owners {
    top: 333px;
  }
  .owner-name {
    font-weight: 700;
    font-size: 17px;
    line-height: 24px;
  }
  .owner-role {
    font-size: 13px;
    line-height: 18px;
  }
  .location {
    top: 432px;
    font-size: 15px;
  }
</style>
</head>
<body>
  <section class="card card--front" aria-label="Business card front">
    <p class="brand-mark">R&amp;B</p>
    <p class="brand-tagline">Music Studio</p>
    <div class="contact">
      <p class="contact-phone">(555) 817-4062</p>
      <p class="contact-web">www.rbtonalartsroom.example</p>
      <p class="contact-email">lorna@rbtonalartsroom.example</p>
    </div>
    <div class="owners">
      <p class="owner-name">Lorna P. Quist</p>
      <p class="owner-name">Oren M. Castaldi</p>
      <p class="owner-role">Owners</p>
    </div>
    <p class="location">Alder Falls, NY</p>
  </section>

  <section class="card card--back" aria-label="Business card back">
    <p class="brand-watermark" aria-hidden="true">R&amp;B</p>
    <p class="brand-tagline">Music Studio</p>
  </section>
</body>
</html>
```